Design a compelling Tarnwove Business Card that will drive people to my site

I want a business card that I can give to people—less to tell them who I am and more to direct them to my website. My website is a portal for Pelmor Aquatics Officials and a place for people who want to become Pelmor Aquatics Officials.
I am uploading my official company logo as well as a business card mockup that I did on my own. Please feel free to completely stray from this design.
I've included a screen recording of the homepage of my website as well.
Target Market(s)
Pelmor Aquatics Officials and people who desire to become one
Contact Information for Business Card
website url
Look and feel
Each slider illustrates characteristics of the customer's brand and the style your logo design should communicate.

```html
<!DOCTYPE html>
<html lang="en">
<head>
<meta charset="utf-8">
<title>Tarnwove Business Card</title>
<link rel="stylesheet" href="https://fonts.googleapis.com/css2?family=Poppins:wght@300;400;600&display=swap">
<style>
  :root {
    --stage: #ecebe8;
    --navy-deep: #0b1450;
    --navy-mid: #1c2a6e;
    --royal: #2f4a9a;
    --brand-navy: #233a93;
    --title-blue: #8fa3d6;
    --ink: #2b2f45;
    --paper: #ffffff;
    --paper-shade: #eeeeef;
  }
  * { box-sizing: border-box; margin: 0; padding: 0; }
  html, body {
    width: 1200px; height: 900px; overflow: hidden;
    background: var(--stage);
    font-family: "Poppins", sans-serif;
  }
  .canvas { position: relative; width: 1200px; height: 900px; }

  .card {
    position: absolute;
    left: 320px;
    width: 560px;
    height: 320px;
    border-radius: 34px;
    overflow: hidden;
    box-shadow: 0 14px 30px rgba(0,0,0,0.18);
  }

  /* Front */
  .card--front {
    top: 80px;
    background: linear-gradient(35deg, var(--royal) 0%, var(--navy-mid) 55%, var(--navy-deep) 100%);
  }
  .front__url {
    position: absolute; top: 30px; right: 34px;
    color: var(--paper);
    font-size: 13px; font-weight: 400;
    letter-spacing: 0.42em;
  }
  .front__brand {
    position: absolute; left: 40px; bottom: 34px;
    display: flex; align-items: center; gap: 14px;
    color: var(--paper);
    font-size: 64px; font-weight: 600; line-height: 1;
    letter-spacing: -0.01em;
  }
  .brand-dot {
    width: 22px; height: 22px; border-radius: 50%;
    background: currentColor;
  }

  /* Back */
  .card--back {
    top: 500px;
    background: linear-gradient(120deg, var(--paper) 0%, var(--paper-shade) 50%, var(--paper) 100%);
  }
  .contact {
    position: absolute; left: 40px; top: 38px;
  }
  .contact__name {
    color: var(--brand-navy);
    font-size: 19px; font-weight: 600; line-height: 1.2;
  }
  .contact__title {
    color: var(--title-blue);
    font-size: 15px; font-weight: 300;
  }
  .contact__rule {
    width: 40px; height: 2px; margin: 12px 0 18px;
    background: var(--brand-navy);
  }
  .contact__list { list-style: none; }
  .contact__item {
    display: flex; align-items: center; gap: 10px;
    color: var(--ink);
    font-size: 15px; font-weight: 300;
    margin-bottom: 8px;
  }
  .contact__icon { width: 16px; height: 16px; flex: none; }
  .back__brand {
    position: absolute; right: 40px; bottom: 70px;
    display: flex; align-items: center; gap: 10px;
    color: var(--brand-navy);
    font-size: 48px; font-weight: 600; line-height: 1;
  }
  .back__brand .brand-dot { width: 16px; height: 16px; }
</style>
</head>
<body>
<main class="canvas">
  <section class="card card--front">
    <p class="front__url">www.tarnwove.com</p>
    <div class="front__brand"><span class="brand-dot"></span>tarnwove</div>
  </section>

  <section class="card card--back">
    <div class="contact">
      <h1 class="contact__name">Marcus Delane</h1>
      <p class="contact__title">CEO &amp; Founder</p>
      <div class="contact__rule"></div>
      <ul class="contact__list">
        <li class="contact__item">
          <svg class="contact__icon" viewBox="0 0 24 24" fill="var(--brand-navy)"><path d="M6.6 10.8a15 15 0 0 0 6.6 6.6l2.2-2.2c.3-.3.7-.4 1-.2 1.1.4 2.3.6 3.6.6.6 0 1 .4 1 1V20c0 .6-.4 1-1 1A17 17 0 0 1 3 4c0-.6.4-1 1-1h3.5c.6 0 1 .4 1 1 0 1.2.2 2.4.6 3.6.1.3 0 .7-.2 1z"/></svg>
          (555) 214-7730
        </li>
        <li class="contact__item">
          <svg class="contact__icon" viewBox="0 0 24 24" fill="var(--brand-navy)"><path d="M2 5h20v14H2z M4 7v.5l8 5 8-5V7l-8 5z" fill-rule="evenodd"/></svg>
          marcus@tarnwove.com
        </li>
        <li class="contact__item">
          <svg class="contact__icon" viewBox="0 0 24 24" fill="none" stroke="var(--brand-navy)" stroke-width="1.8"><circle cx="12" cy="12" r="9"/><path d="M3 12h18M12 3c3 3 3 15 0 18M12 3c-3 3-3 15 0 18"/></svg>
          www.tarnwove.com
        </li>
      </ul>
    </div>
    <div class="back__brand"><span class="brand-dot"></span>tarnwove</div>
  </section>
</main>
</body>
</html>
```